New Business Cards for Tormin Group

We need a new Business Card to compliment our new logo. We are a vibrant design, manufacture and install business providing recreation areas, public parks and Municipal spaces. We want business cards that are classy, modern and clean.

We have recently changed our logo, and are celebrating our 40th anniversary. We want business cards with a new modern design to reflect our status.

Target Market(s)

Customers

Contact Information for Business Card

We need all the details of our 3 offices as per the business card attached. Please disregard the old logo on the business card, the other three files show our new logo.

Requirements
Must have
• All info as per attached business card but with new logo.
Nice to have

```html
<!DOCTYPE html>
<html lang="en">
<head>
<meta charset="utf-8">
<title>Tormin Group – Business Card</title>
<link rel="stylesheet" href="https://fonts.googleapis.com/css2?family=Barlow:wght@400;600;700&display=swap">
<style>
  :root {
    --backdrop: #e6e6e6;
    --card: #ffffff;
    --brand-red: #e8333a;
    --ink: #3a3a3c;
    --rule: #4a4a4a;
  }
  * { box-sizing: border-box; margin: 0; padding: 0; }
  html, body {
    width: 1200px; height: 914px; overflow: hidden;
    background: var(--backdrop);
    font-family: "Barlow", Arial, sans-serif;
    color: var(--ink);
  }
  .card {
    position: absolute; left: 100px; top: 171px;
    width: 1000px; height: 572px;
    background: var(--card);
    box-shadow: 0 10px 30px rgba(0,0,0,.18);
    overflow: hidden;
  }
  .brand {
    position: absolute; right: 70px; top: 50px;
    display: flex; align-items: center; gap: 18px;
  }
  .brand-dot {
    width: 110px; height: 110px; border-radius: 50%;
    background: var(--brand-red); flex: none;
  }
  .brand-name {
    font-weight: 700; font-size: 40px; letter-spacing: 1px;
    color: var(--ink); line-height: 1; white-space: nowrap;
  }
  .accent-bar {
    position: absolute; left: 0; top: 196px;
    width: 34px; height: 54px; background: var(--brand-red);
  }
  .person { position: absolute; left: 64px; top: 186px; }
  .person-name {
    font-weight: 700; font-size: 38px; color: var(--brand-red);
    letter-spacing: .5px; line-height: 42px;
  }
  .person-title { font-size: 22px; line-height: 28px; margin-bottom: 10px; }
  .contact-list { list-style: none; }
  .contact-list li {
    display: flex; align-items: center; gap: 12px;
    font-size: 20px; line-height: 26px; white-space: nowrap;
  }
  .icon { width: 17px; height: 17px; flex: none; fill: var(--brand-red); }
  .divider {
    position: absolute; left: 64px; right: 40px; top: 362px;
    height: 2px; background: var(--rule); border: 0;
  }
  .offices {
    position: absolute; left: 72px; top: 380px; right: 40px;
    display: grid; grid-template-columns: repeat(3, 1fr); column-gap: 12px;
  }
  .office-name {
    font-weight: 600; font-size: 23px; line-height: 28px;
    color: var(--brand-red); margin-bottom: 2px;
  }
  .office-address { font-size: 20px; line-height: 26px; margin-bottom: 6px; }
</style>
</head>
<body>
<svg width="0" height="0" style="position:absolute">
  <symbol id="i-phone" viewBox="0 0 24 24"><path d="M6.6 10.8a15.5 15.5 0 0 0 6.6 6.6l2.2-2.2a1 1 0 0 1 1-.25 11.4 11.4 0 0 0 3.6.6 1 1 0 0 1 1 1V20a1 1 0 0 1-1 1A17 17 0 0 1 3 4a1 1 0 0 1 1-1h3.5a1 1 0 0 1 1 1c0 1.25.2 2.45.6 3.6a1 1 0 0 1-.25 1z"/></symbol>
  <symbol id="i-mobile" viewBox="0 0 24 24"><path d="M7 1h10a2 2 0 0 1 2 2v18a2 2 0 0 1-2 2H7a2 2 0 0 1-2-2V3a2 2 0 0 1 2-2zm0 3v14h10V4z"/></symbol>
  <symbol id="i-web" viewBox="0 0 24 24"><circle cx="12" cy="12" r="11"/><circle cx="12" cy="12" r="4" fill="#fff"/></symbol>
  <symbol id="i-fax" viewBox="0 0 24 24"><path d="M6 2h12v6H6zM2 9h20v9h-4v4H6v-4H2zm6 7v4h8v-4z"/></symbol>
  <symbol id="i-mail" viewBox="0 0 24 24"><path d="M2 5h20v14H2zm2 2v.5l8 5.5 8-5.5V7z"/></symbol>
</svg>

<main class="card">
  <div class="brand">
    <span class="brand-dot"></span>
    <span class="brand-name">TORMIN GROUP</span>
  </div>

  <span class="accent-bar"></span>
  <section class="person">
    <h1 class="person-name">Sami Haddar</h1>
    <p class="person-title">Managing Partner</p>
    <ul class="contact-list">
      <li><svg class="icon"><use href="#i-phone"/></svg>+971 (0)50 384 7120</li>
      <li><svg class="icon"><use href="#i-mobile"/></svg>sami@tormingroup.com</li>
      <li><svg class="icon"><use href="#i-web"/></svg>www.tormingroup.com</li>
    </ul>
  </section>

  <hr class="divider">

  <section class="offices">
    <div class="office">
      <h2 class="office-name">Head office</h2>
      <p class="office-address">41208 Abu Dhabi, U.A.E</p>
      <ul class="contact-list">
        <li><svg class="icon"><use href="#i-phone"/></svg>+971 (0)2 5180372</li>
        <li><svg class="icon"><use href="#i-fax"/></svg>+971 (0)2 5180373</li>
        <li><svg class="icon"><use href="#i-mail"/></svg>sales@tormingroup.com</li>
      </ul>
    </div>
    <div class="office">
      <h2 class="office-name">Dubai Office</h2>
      <p class="office-address">217460 Dubai, U.A.E.</p>
      <ul class="contact-list">
        <li><svg class="icon"><use href="#i-phone"/></svg>+971 (0)4 3926058</li>
        <li><svg class="icon"><use href="#i-fax"/></svg>+971 (0)4 3926059</li>
        <li><svg class="icon"><use href="#i-mail"/></svg>sales@tormingroup.com</li>
      </ul>
    </div>
    <div class="office">
      <h2 class="office-name">Qatar Office</h2>
      <p class="office-address">30871 Doha, Qatar</p>
      <ul class="contact-list">
        <li><svg class="icon"><use href="#i-phone"/></svg>+974 40527318</li>
        <li><svg class="icon"><use href="#i-fax"/></svg>+974 40527319</li>
        <li><svg class="icon"><use href="#i-mail"/></svg>sales@tormingroup.com</li>
      </ul>
    </div>
  </section>
</main>
</body>
</html>
```